Our Premium Canadian Organic Hemp Oil needs a clean, modern label design!

Design a label for organic hemp oil bottle. Max three colours. Clean white background. The over all style and concept needs to work for future products and other packaging. As an example, hemp seed, or beverage.
Bottle is 2 1/4 inches in diameter and 9 inches from bottom to the neck, 11 inches in total. 500ml.
The design is Clean, simple, sophisticated, modern label design. We would like a simple botanical drawing of hemp plant and seeds (no buds).
Certiva Bio symbol - see below
Vegan symbol
Paleo

The back of the bottle should have the following description below and the nutritional data provided in the attachments.
“This is Vela Tundris
In our quest to find foods with the highest purity, nutritional density, and sustainability, we discovered and fell in love with the pristine Boreal region of Quebec. This land is protected by the beautiful Laurentian Mountain Ranges and is known to produce plants of particularly high nutritional composition.
The natural harmony of the Boreal region and its ecosystem protects the vegetation from a variety of common pests and diseases. These natural barriers removes the need for impurities such as GMOs and harmful sprays.

Nourish from Within!
Our hemp oil quenches thirsty cells with abundant essential fatty acids that alleviate dry skin, hair and nails, boosts metabolism and immunity, and regulates hormones and blood pressure.

Try on salads, drizzle on pasta, garnish dips, add to smoothies or take by the tablespoon.
“Goodness by the spoonful”

“Part of a healthy and balanced diet” above the nutritional data chart

Target Market(s)

Canada & USA, Products for consumers seeking superior quality product from artisan farms.

Font styles to use
Serif
Sans Serif
Decorative

Colors

Designer to choose colors to be used in the design.

Requirements
Must have
• The design is for the front sticker label, we will award the winning designer with the extended works to do the back sticker and the additional products. We like the fonts and spacing used by the Orrin & Pell brand, provided below as inspiration.
• Brand name: “Vela Tundris”
• Slogan: “Finely crafted hemp foods”
• “Cold pressed Organic Hemp Oil”
• Brief Description: “Luxurious locks & radiant skin, beauty comes from within.
• Our artisan organic hemp oil quenches thirsty cells with full spectrum plant based Omega 3 & 6”
• Certiva Bio symbol - see below
• Vegan symbol
• Paleo
Nice to have
• We like the Orrin & Pell sticker seal and imagine “N 48” in the circle of the sticker and “Organically Yours” written on the length of the seal sticker.
Should not have
• We want our product to stand out from the competitors so we are vearing away from the styling of other brands.

```html
<!DOCTYPE html>
<html lang="en">
<head>
<meta charset="utf-8">
<title>Vela Tundris — Cold Pressed Organic Hemp Oil Label</title>
<link href="https://fonts.googleapis.com/css2?family=Marcellus&family=Noticia+Text:ital,wght@0,400;0,700;1,400;1,700&display=swap" rel="stylesheet">
<style>
  :root {
    --bg: #d9d9d9;
    --paper: #ffffff;
    --leaf: #8aac45;
    --forest: #3f5220;
    --ink: #4a4a4a;
    --cream: #f4f7ec;
  }
  * { margin: 0; padding: 0; box-sizing: border-box; }
  html, body { width: 1134px; height: 1200px; overflow: hidden; }
  body {
    background: var(--bg);
    font-family: "Noticia Text", Georgia, serif;
    position: relative;
  }
  .label-stage {
    position: absolute;
    left: 380px; top: 38px;
    width: 466px; height: 1405px;
    transform: scale(0.8);
    transform-origin: top left;
  }
  .seal-strip {
    position: absolute;
    left: 208px; top: 0;
    width: 50px; height: 480px;
    background: var(--leaf);
  }
  .seal-strip::after {
    content: "";
    position: absolute;
    inset: 0 4px;
    border-left: 2px dotted rgba(255,255,255,.85);
    border-right: 2px dotted rgba(255,255,255,.85);
  }
  .seal-motto {
    position: absolute;
    left: 25px; top: 260px;
    transform: translate(-50%, -50%) rotate(-90deg);
    white-space: nowrap;
    color: var(--paper);
    font-style: italic;
    font-weight: 700;
    font-size: 20px;
    letter-spacing: 4px;
  }
  .label {
    position: absolute;
    left: 0; top: 475px;
    width: 466px; height: 930px;
    background: var(--paper);
    overflow: hidden;
  }
  .seal-disc {
    position: absolute;
    left: 184px; top: 427px;
    width: 96px; height: 96px;
    border-radius: 50%;
    background: var(--leaf);
    z-index: 3;
    display: flex; align-items: center; justify-content: center;
  }
  .seal-disc::after {
    content: "";
    position: absolute; inset: 5px;
    border-radius: 50%;
    border: 2px dotted rgba(255,255,255,.85);
  }
  .seal-degree {
    color: var(--paper);
    font-style: italic;
    font-size: 34px;
  }
  .brand-box {
    position: absolute;
    left: 77px; top: 101px;
    width: 312px; height: 70px;
    border: 2px solid var(--ink);
    display: flex; align-items: center; justify-content: center;
    font-family: "Marcellus", serif;
    font-size: 46px;
    color: var(--ink);
  }
  .brand-slogan {
    position: absolute;
    left: 0; right: 0; top: 183px;
    text-align: center;
    font-style: italic;
    font-size: 19px;
    letter-spacing: 2px;
    color: #333;
  }
  .green-band {
    position: absolute;
    left: 0; top: 483px;
    width: 100%; height: 395px;
    background: var(--leaf);
  }
  .botanical {
    position: absolute;
    left: 45px; top: 235px;
    width: 375px; height: 340px;
    border-radius: 40% 45% 30% 40%;
    background: radial-gradient(ellipse at center, rgba(120,120,120,.22), rgba(120,120,120,.06) 65%, rgba(120,120,120,0) 75%);
    z-index: 2;
  }
  .product-kicker {
    position: absolute; left: 0; right: 0; top: 576px;
    text-align: center;
    color: var(--paper);
    font-size: 18px; letter-spacing: 1px;
  }
  .product-name {
    position: absolute; left: 0; right: 0; top: 596px;
    text-align: center;
    color: var(--paper);
    font-size: 26px; letter-spacing: 2px;
  }
  .product-promise {
    position: absolute; left: 0; right: 0; top: 638px;
    text-align: center;
    color: var(--cream);
    font-style: italic;
    font-size: 17px; line-height: 22px;
    letter-spacing: 1.5px;
  }
  .product-story {
    position: absolute;
    right: 203px; top: 694px;
    width: 220px;
    text-align: right;
    color: var(--paper);
    font-style: italic; font-weight: 700;
    font-size: 16px; line-height: 22px;
  }
  .claim-icons {
    position: absolute;
    left: 300px; top: 697px;
    width: 100px;
    display: grid;
    grid-template-columns: 50px 50px;
    row-gap: 6px;
  }
  .claim {
    display: flex; flex-direction: column; align-items: center;
    color: var(--paper);
    font-size: 8px; letter-spacing: .3px;
  }
  .claim svg { width: 40px; height: 40px; }
  .volume {
    position: absolute;
    left: 84px; top: 830px;
    padding-left: 10px;
    border-left: 3px solid var(--paper);
    color: var(--paper);
    font-style: italic; font-weight: 700;
    font-size: 17px; line-height: 26px;
  }
  .cert-badge {
    position: absolute;
    left: 316px; top: 812px;
    width: 60px; height: 46px;
    border-radius: 50%;
    background: var(--forest);
    opacity: .75;
  }
  .origin-band {
    position: absolute;
    left: 0; top: 878px;
    width: 100%; height: 52px;
    background: var(--forest);
    color: var(--paper);
    text-align: center;
    font-style: italic;
    padding-top: 6px;
  }
  .origin-band .steps { font-size: 14px; letter-spacing: 1.5px; line-height: 17px; }
  .origin-band .region { font-size: 13px; letter-spacing: .8px; line-height: 17px; }
</style>
</head>
<body>
  <div class="label-stage">
    <div class="seal-strip">
      <span class="seal-motto">Organically Yours</span>
    </div>
    <div class="seal-disc"><span class="seal-degree">48°</span></div>

    <section class="label">
      <div class="green-band"></div>
      <div class="brand-box">Vela Tundris</div>
      <p class="brand-slogan">Finely crafted hemp foods</p>
      <div class="botanical" role="img" aria-label="Fine line botanical drawing of a hemp plant with leaves and seeds"></div>

      <p class="product-kicker">COLD PRESSED</p>
      <h1 class="product-name">ORGANIC HEMP OIL</h1>
      <p class="product-promise">Luscious Locks &amp; Radiant Skin.<br>Nourish your cells from within.</p>

      <p class="product-story">Our artisan organic hemp oil quenches thirsty cells with full spectrum plant based Omega 3 &amp; 6</p>

      <div class="claim-icons">
        <div class="claim">
          <svg viewBox="0 0 40 40" fill="none" stroke="#fff" stroke-width="1.6"><circle cx="20" cy="20" r="17"/><path d="M20 30V12M20 16l-4-3M20 20l-4-3M20 24l-4-3M20 16l4-3M20 20l4-3M20 24l4-3"/><path d="M9 9l22 22"/></svg>
          <span>PALEO</span>
        </div>
        <div class="claim">
          <svg viewBox="0 0 40 40" fill="none" stroke="#fff" stroke-width="1.6"><circle cx="20" cy="20" r="17"/><path d="M10 20h20a10 8 0 0 1-20 0z"/><path d="M20 19c0-5 3-7 6-8M20 19c-1-4-4-6-7-6"/></svg>
          <span>RAW</span>
        </div>
        <div class="claim">
          <svg viewBox="0 0 40 40" fill="none" stroke="#fff" stroke-width="1.6"><circle cx="20" cy="20" r="17"/><path d="M12 28c0-10 6-16 16-17-1 10-7 17-16 17zM12 28l9-10"/></svg>
          <span>VEGAN</span>
        </div>
        <div class="claim">
          <svg viewBox="0 0 40 40" fill="none" stroke="#fff" stroke-width="1.6"><circle cx="20" cy="20" r="17"/><path d="M20 30V16M20 20c-4 0-6-3-6-6 4 0 6 3 6 6zM20 18c4 0 6-3 6-6-4 0-6 3-6 6z"/><path d="M9 9l22 22"/></svg>
          <span>GMO FREE</span>
        </div>
      </div>

      <p class="volume">500ml</p>
      <div class="cert-badge" role="img" aria-label="Certification badge"></div>

      <footer class="origin-band">
        <p class="steps">GROWN • PRESSED • BOTTLED</p>
        <p class="region">In the pristine Boreal region of Canada</p>
      </footer>
    </section>
  </div>
</body>
</html>
```